Web design for Crowdfunding site HopeWingsRally.com

We need a web design for christian crowdfunding website. Here is the challenge: We need responsive layout that is targeted first in iPad size of screen. It should also scale somehow down to iPhone size of screens. Web layout can be about the same size as iPad screen.

Screens should work so that main page scrolls not but only certain part of the screen scrolls and always one "page" at time. We can implement these "scrolls" then later with javascript but now we need only design. The challenge is to create this kind of hybrid website / app look.

Target is at first to raise funds to orphan people needing about $40 per month for their living and education. There is always some organization which takes care of these kids. Later there will be other christian missions included. At first we are looking to find monthly supporters.

You can be as creative as you want :) As you see from the look and feel sector, I am not looking any same traditional look which many "help kids" sites have. I am looking to reach now younger generation and therefore iPad and mobile are the main screen sizes.

Inspirational designs:
- https://example-gallery.test/profiles/studiofernlake/designs/482716?from=%2Fbrowse%2Fxhr%2Fdesigns%3Fcategory%3Dmobile-app-design
- http://www.artpoolhub.test/design/8261047 Clear, simple visuals
- http://www.artpoolhub.test/design/7394215 Header
- http://www.artpoolhub.test/design/6048392 Contrast in the colors, i think is powerfull

Some terms could be: Kids play, kids are learning (in the school). No static posture but living like kids are. I wonder also how we could also add little bit gaming style even though the question is of reali life of real people. Giving should be rewarding.

Target Market(s)

People who want help other people.

Industry/Entity Type

Christian

Number of Pages Required

4 page

Requirements
Must have
• Homepage. Mission page (In my wireframes it was one kid).
Nice to have
• Other pages and some idea how to scroll. 4 pages is no must. If you feel easy, please give first some draft and I give comments on that.

```html
<!DOCTYPE html>
<html lang="en">
<head>
<meta charset="utf-8">
<title>Hope Wings Rally – Mission: Orphan Maria</title>
<link href="https://fonts.googleapis.com/css2?family=Roboto:wght@400;500;700&display=swap" rel="stylesheet">
<style>
  :root{
    --yellow:#fdc00f;
    --yellow-deep:#d49a00;
    --header:#2a2a2a;
    --page:#000;
    --panel:#fff;
    --ink:#1e1e1e;
    --ink-soft:#444;
    --ring-track:#c5c9cd;
    --check:#e6e6e6;
    --check-border:#b5b5b5;
    --timeline:#333;
  }
  *{box-sizing:border-box;margin:0;padding:0}
  html,body{width:1200px;height:900px;overflow:hidden}
  body{background:var(--page);font-family:"Roboto",Arial,sans-serif;color:var(--ink);position:relative}

  /* Top navigation */
  .topbar{position:absolute;left:0;top:0;width:1200px;height:73px;background:var(--header);color:#fff}
  .menu-toggle{position:absolute;left:29px;top:22px;display:flex;align-items:center;gap:16px;font-size:26px;font-weight:500;letter-spacing:.2px}
  .search-btn{position:absolute;left:314px;top:13px;width:46px;height:46px;border:2px solid #fff;border-radius:50%;display:flex;align-items:center;justify-content:center}
  .brand{position:absolute;left:0;right:0;top:17px;text-align:center;color:var(--yellow);font-size:33px;font-weight:500;letter-spacing:.5px;pointer-events:none}
  .btn-login,.btn-signup{position:absolute;top:13px;height:47px;display:flex;align-items:center;justify-content:center;font-size:20px;font-weight:500}
  .btn-login{left:921px;width:117px;border:2px solid #fff;border-radius:3px}
  .btn-signup{left:1050px;width:120px;background:var(--yellow);border-radius:3px}

  /* Mission bar */
  .mission-bar{position:absolute;left:0;top:73px;width:1200px;height:84px;background:var(--yellow);color:var(--ink)}
  .mission-title,.mission-name{position:absolute;top:26px;font-size:28px;font-weight:500}
  .mission-title{left:29px}
  .mission-name{left:768px}
  .mission-links{position:absolute;left:1062px;top:32px;display:flex;gap:9px;align-items:center}
  .share-dot{width:17px;height:17px;background:var(--ink);border-radius:3px}

  /* Story panel */
  .story-panel{position:absolute;left:29px;top:185px;width:716px;height:682px;background:var(--panel);border-radius:3px}
  .tabs{position:absolute;left:19px;top:20px;display:flex;gap:15px}
  .tab{width:217px;height:64px;border:2px solid var(--ink);border-radius:2px;display:flex;align-items:center;justify-content:center;font-size:25px;font-weight:500}
  .tab.is-active{background:linear-gradient(var(--yellow),var(--yellow-deep));border-color:var(--yellow-deep)}
  .timeline{position:absolute;left:29px;top:168px;width:3px;height:429px;background:var(--timeline)}
  .timeline-dot{position:absolute;left:24px;width:13px;height:13px;border-radius:50%;background:var(--timeline)}
  .timeline-dot.is-current{left:21px;width:20px;height:20px;background:var(--yellow)}
  .story-text{position:absolute;left:67px;width:631px;font-size:16.4px;line-height:26px;text-align:justify;color:var(--ink)}
  .story-text p+p{margin-top:10px}
  .story-photo{position:absolute;left:67px;top:304px;width:631px;height:165px;background:linear-gradient(135deg,#8e99a6 0%,#c9d6e6 45%,#e9eef4 55%,#7f8a96 100%)}

  /* Side panel */
  .side-panel{position:absolute;left:768px;top:185px;width:402px;height:682px;background:var(--panel);border-radius:3px;overflow:hidden}
  .location{position:absolute;left:17px;top:20px;font-size:20px;font-weight:500;line-height:37px}
  .location-row{display:flex;align-items:center;gap:11px}
  .location .org{padding-left:25px}
  .band{position:absolute;left:0;width:402px;height:62px;background:var(--yellow);display:flex;align-items:center;padding-left:17px;font-size:22px;font-weight:500}
  .band.support{top:99px}
  .band.participate{top:358px}
  .supporters{position:absolute;right:10px;top:12px;display:flex;gap:9px;align-items:center}
  .supporter{width:38px;height:38px;border-radius:50%;background:#fff;border:3px solid #fff;box-shadow:inset 0 0 0 14px var(--ink)}
  .my-support{position:absolute;left:17px;top:177px;font-size:20.5px;font-weight:500;color:#333}
  .progress{position:absolute;left:16px;top:219px}
  .progress-meta{position:absolute;left:150px;top:228px}
  .given{font-size:20px;font-weight:500}
  .needed{font-size:17px;color:#555;margin-top:10px}
  .per-month{font-size:18px;margin-top:13px;display:flex;align-items:center;gap:8px}
  .options{position:absolute;left:17px;top:442px;width:372px;list-style:none}
  .option{display:flex;align-items:center;height:47px;font-size:18.5px;font-weight:500}
  .checkbox{width:26px;height:26px;border:1px solid var(--check-border);background:var(--check);border-radius:4px;margin-right:11px}
  .option .amount-input{font-size:16.5px;font-weight:400;color:#333;margin-left:20px}
  .cart{margin-left:auto}
</style>
</head>
<body>

<header class="topbar">
  <div class="menu-toggle">
    <svg width="28" height="28" viewBox="0 0 28 28" fill="#fff"><rect x="0" y="2" width="5" height="4"/><rect x="9" y="2" width="19" height="4"/><rect x="0" y="12" width="5" height="4"/><rect x="9" y="12" width="19" height="4"/><rect x="0" y="22" width="5" height="4"/><rect x="9" y="22" width="19" height="4"/></svg>
    <span>SEE THE MISSIONS</span>
  </div>
  <div class="search-btn">
    <svg width="22" height="22" viewBox="0 0 22 22" fill="none" stroke="#fff" stroke-width="3"><circle cx="9" cy="9" r="6.5"/><line x1="14" y1="14" x2="20" y2="20"/></svg>
  </div>
  <div class="brand">HOPE WINGS RALLY</div>
  <div class="btn-login">LOGIN</div>
  <div class="btn-signup">SIGNUP</div>
</header>

<section class="mission-bar">
  <h1 class="mission-title">Mission: Orphan Maria, 11y</h1>
  <div class="mission-name">Name: Maria, 11y</div>
  <div class="mission-links">
    <svg width="26" height="20" viewBox="0 0 26 20" fill="none" stroke="#1e1e1e" stroke-width="2"><path d="M1 3h8c2 0 4 1 4 3v13c0-2-2-3-4-3H1z"/><path d="M25 3h-8c-2 0-4 1-4 3v13c0-2 2-3 4-3h8z"/></svg>
    <span class="share-dot"></span>
    <span class="share-dot"></span>
    <span class="share-dot"></span>
  </div>
</section>

<main class="story-panel">
  <nav class="tabs">
    <div class="tab is-active">Story</div>
    <div class="tab">Updates</div>
    <div class="tab">Comments</div>
  </nav>

  <div class="timeline"></div>
  <span class="timeline-dot" style="top:162px"></span>
  <span class="timeline-dot is-current" style="top:399px"></span>
  <span class="timeline-dot" style="top:590px"></span>

  <div class="story-text" style="top:87px">
    <p>Nemo enim ipsam voluptatem quia voluptas sit aspernatur aut odit aut fugit, sed quia consequuntur magni dolores eos qui ratione voluptatem sequi nesciunt. Neque porro quisquam est, qui dolorem ipsum</p>
    <p>Nemo enim ipsam voluptatem quia voluptas sit aspernatur aut odit aut fugit, sed quia consequuntur magni dolores eos qui ratione voluptatem sequi nesciunt. Neque porro quisquam est, qui dolorem ipsum</p>
  </div>

  <div class="story-photo" role="img" aria-label="Photo of smiling volunteers joining hands in a circle against the sky"></div>

  <div class="story-text" style="top:487px">
    <p>Nemo enim ipsam voluptatem quia voluptas sit aspernatur aut odit aut fugit, sed quia consequuntur magni dolores eos qui ratione voluptatem sequi nesciunt. Neque porro quisquam est, qui dolorem ipsum</p>
    <p>Nemo enim ipsam voluptatem quia voluptas sit aspernatur aut odit aut fugit, sed quia consequuntur magni dolores eos qui ratione voluptatem sequi nesciunt. Neque porro quisquam est, qui dolorem ipsum</p>
  </div>
</main>

<aside class="side-panel">
  <div class="location">
    <div class="location-row">
      <svg width="14" height="20" viewBox="0 0 14 20"><path d="M7 0C3 0 0 3 0 7c0 5 7 13 7 13s7-8 7-13c0-4-3-7-7-7z" fill="#1e1e1e"/><circle cx="7" cy="7" r="2.6" fill="#fff"/></svg>
      <span>Kalkutta</span>
    </div>
    <div class="org">Organization: Jacob</div>
  </div>

  <div class="band support">
    Support
    <div class="supporters">
      <span class="supporter"></span><span class="supporter"></span><span class="supporter"></span><span class="supporter"></span>
      <svg width="14" height="24" viewBox="0 0 14 24" fill="none" stroke="#1e1e1e" stroke-width="3"><path d="M2 2l10 10L2 22"/></svg>
    </div>
  </div>

  <div class="my-support">My support is now: $5 / month</div>

  <svg class="progress" width="116" height="116" viewBox="0 0 116 116">
    <defs><linearGradient id="ringFill" x1="0" y1="0" x2="0" y2="1"><stop offset="0" stop-color="#fdc00f"/><stop offset="1" stop-color="#c98f00"/></linearGradient></defs>
    <circle cx="58" cy="58" r="52" fill="none" stroke="var(--ring-track)" stroke-width="8"/>
    <circle cx="58" cy="58" r="52" fill="none" stroke="url(#ringFill)" stroke-width="8" stroke-dasharray="147 327" transform="rotate(-90 58 58)"/>
    <text x="58" y="67" text-anchor="middle" font-family="Roboto, Arial, sans-serif" font-size="26" fill="#1e1e1e">45%</text>
  </svg>

  <div class="progress-meta">
    <div class="given">$15 given</div>
    <div class="needed">of total $35 needed</div>
    <div class="per-month">
      <svg width="17" height="17" viewBox="0 0 17 17" fill="none" stroke="#1e1e1e" stroke-width="1.6"><rect x="1" y="3" width="15" height="13"/><line x1="1" y1="7" x2="16" y2="7"/><line x1="5" y1="1" x2="5" y2="4"/><line x1="12" y1="1" x2="12" y2="4"/><path d="M4 10h2M8 10h2M12 10h2M4 13h2M8 13h2M12 13h2"/></svg>
      per month need
    </div>
  </div>

  <div class="band participate">Participate</div>

  <ul class="options">
    <li class="option"><span class="checkbox"></span>I am in, $1 / month<svg class="cart" width="30" height="24" viewBox="0 0 30 24" fill="#1e1e1e"><path d="M0 1h5l4 14h16l4-11H8" fill="none" stroke="#1e1e1e" stroke-width="2.2"/><path d="M9 7h18M10 11h16" stroke="#1e1e1e" stroke-width="1.4"/><circle cx="11" cy="20.5" r="2.3"/><circle cx="23" cy="20.5" r="2.3"/></svg></li>
    <li class="option"><span class="checkbox"></span>Increased, $5 / month<svg class="cart" width="30" height="24" viewBox="0 0 30 24" fill="#1e1e1e"><path d="M0 1h5l4 14h16l4-11H8" fill="none" stroke="#1e1e1e" stroke-width="2.2"/><path d="M9 7h18M10 11h16" stroke="#1e1e1e" stroke-width="1.4"/><circle cx="11" cy="20.5" r="2.3"/><circle cx="23" cy="20.5" r="2.3"/></svg></li>
    <li class="option"><span class="checkbox"></span>Decent help, $10 / month<svg class="cart" width="30" height="24" viewBox="0 0 30 24" fill="#1e1e1e"><path d="M0 1h5l4 14h16l4-11H8" fill="none" stroke="#1e1e1e" stroke-width="2.2"/><path d="M9 7h18M10 11h16" stroke="#1e1e1e" stroke-width="1.4"/><circle cx="11" cy="20.5" r="2.3"/><circle cx="23" cy="20.5" r="2.3"/></svg></li>
    <li class="option"><span class="checkbox"></span>Whole Kid, $35 / month<svg class="cart" width="30" height="24" viewBox="0 0 30 24" fill="#1e1e1e"><path d="M0 1h5l4 14h16l4-11H8" fill="none" stroke="#1e1e1e" stroke-width="2.2"/><path d="M9 7h18M10 11h16" stroke="#1e1e1e" stroke-width="1.4"/><circle cx="11" cy="20.5" r="2.3"/><circle cx="23" cy="20.5" r="2.3"/></svg></li>
    <li class="option"><span class="checkbox"></span>My amount<span class="amount-input">Enter amount</span><svg class="cart" width="30" height="24" viewBox="0 0 30 24" fill="#1e1e1e"><path d="M0 1h5l4 14h16l4-11H8" fill="none" stroke="#1e1e1e" stroke-width="2.2"/><path d="M9 7h18M10 11h16" stroke="#1e1e1e" stroke-width="1.4"/><circle cx="11" cy="20.5" r="2.3"/><circle cx="23" cy="20.5" r="2.3"/></svg></li>
  </ul>
</aside>

</body>
</html>
```